2 Page Brochure Design Project

I have attached a 2 page word document. I want this document made into a more professional and quality looking document. The colours / look and feel must be in line with a .pdf document I have attached.
I do not have the raw image files from the attached word document and realise that in the designed brochure, they resolution will be poor. Just use what I have provided and I will add my own pictures as layer in substitute for these ones later on myself.
Target Market(s)
Mining Sector
Industry/Entity Type
It Professional
Requirements
Must have
- 1. Must have same look and feel as attached .pdf. It does not need the black and white truck, but must be similar in effects.
2. Must be created in Photoshop (other packages not acceptable).
3. All source files including any 3rd party images must be provided by the successful designer.
4. Although the photo's are different sizes in the attached word document, I would prefer them to be the same size in the brochure, but this is not essential.
5. A4 size for each page
6. High Res as this will be printed. I can make it lower quality for web publishing later.

```html
<!DOCTYPE html>
<html lang="en">
<head>
<meta charset="utf-8">
<title>ID Label Installation Guide – Steps 04 to 10</title>
<link rel="stylesheet" href="https://fonts.googleapis.com/css2?family=Anton&family=Roboto+Condensed:wght@700&family=Arimo:ital,wght@0,400;0,700;1,400&display=swap">
<style>
:root{
  --brand-yellow:#ffe600;
  --ink:#111111;
  --paper:#ffffff;
  --frame:#5a5a5a;
  --photo-dark:#2a2a24;
  --photo-light:#d9d6cf;
}
*{margin:0;padding:0;box-sizing:border-box}
html,body{width:927px;height:1200px;overflow:hidden}
body{background:var(--brand-yellow);position:relative;font-family:"Arimo",Arial,sans-serif;color:var(--ink)}
.sheet{position:absolute;left:55px;top:66px;width:817px;height:1067px;background:var(--paper)}
.step{position:absolute;border:1px solid var(--frame);background:var(--paper)}
.step-number{position:absolute;top:0;width:53px;height:56px;background:var(--brand-yellow);color:var(--paper);
  font-family:"Anton",Impact,sans-serif;font-size:30px;line-height:56px;text-align:center;letter-spacing:.5px;z-index:2}
.photo{position:absolute}
.photo.dark{background:linear-gradient(160deg,#3a3a32 0%,var(--photo-dark) 55%,#4e5a1e 100%)}
.photo.light{background:linear-gradient(160deg,#eeece8 0%,var(--photo-light) 100%)}
.photo.mixed{background:linear-gradient(90deg,var(--photo-dark) 0%,#353a22 60%,#e8e6e1 60%,#eeece8 100%)}
.step-text{position:absolute;font-size:14.6px;line-height:18.3px;white-space:nowrap}
.step-note{position:absolute;font-size:14.2px;line-height:17.5px;font-style:italic;white-space:nowrap}
.brand-plate{position:absolute;left:610px;top:907px;width:238px;height:48px;background:var(--ink);
  color:var(--brand-yellow);font-family:"Roboto Condensed",Arial,sans-serif;font-weight:700;font-size:24px;
  line-height:48px;text-align:center;letter-spacing:1px;text-transform:uppercase}
.contact-list{position:absolute;left:610px;top:978px;list-style:none;font-family:"Roboto Condensed",Arial,sans-serif;
  font-weight:700;font-size:15.5px;line-height:21.5px;white-space:nowrap}
.contact-list li{position:relative;padding-left:22px}
.contact-list li::before{content:"";position:absolute;left:0;top:5px;width:12px;height:12px;background:var(--brand-yellow)}
.contact-list .cont::before{display:none}
.site-address{position:absolute;left:55px;top:1142px;font-family:"Arimo",Arial,sans-serif;font-weight:700;font-size:23px}
</style>
</head>
<body>
<div class="sheet"></div>

<section class="step" style="left:86px;top:92px;width:234px;height:323px">
  <div class="step-number" style="left:27px">04</div>
  <div class="photo dark" role="img" aria-label="Hands taping a black ID label with yellow lettering to a wall" style="left:16px;top:20px;width:198px;height:151px"></div>
  <p class="step-text" style="left:16px;top:182px">When you are happy with<br>the position of the ID label,<br>place a strip of masking<br>tape vertically across the full<br>length of the ID Label just<br>past centre to ensure the<br>label doesn’t move.</p>
</section>

<section class="step" style="left:345px;top:92px;width:234px;height:323px">
  <div class="step-number" style="left:28px">05</div>
  <div class="photo mixed" role="img" aria-label="Cutting the masking tape tab at the label edge" style="left:16px;top:20px;width:199px;height:96px"></div>
  <div class="photo light" role="img" aria-label="Label folded back halfway showing its backing paper" style="left:16px;top:128px;width:199px;height:93px"></div>
  <p class="step-text" style="left:11px;top:232px">Cut the masking tape tab on the<br>right side edge of the sticker so<br>you can fold the sticker back<br>toward you half way.</p>
</section>

<section class="step" style="left:604px;top:92px;width:234px;height:323px">
  <div class="step-number" style="left:23px">06</div>
  <div class="photo light" role="img" aria-label="Scissors trimming backing paper peeled from the label" style="left:13px;top:20px;width:199px;height:212px"></div>
  <p class="step-text" style="left:13px;top:250px">Peel the backing paper off the<br>label, cutting the excess paper<br>off with your scissors.</p>
</section>

<section class="step" style="left:86px;top:447px;width:234px;height:323px">
  <div class="step-number" style="left:27px">07</div>
  <div class="photo mixed" role="img" aria-label="Installer laying the label back onto the wall surface" style="left:16px;top:20px;width:198px;height:202px"></div>
  <p class="step-text" style="left:16px;top:236px">Lay the label back on to the<br>surface carefully realigning<br>your masking tape to ensure<br>your label is straight.</p>
</section>

<section class="step" style="left:345px;top:447px;width:493px;height:323px">
  <div class="step-number" style="left:28px">08</div>
  <div class="photo dark" role="img" aria-label="Squeegee smoothing the label while the right edge is held off the wall" style="left:16px;top:20px;width:209px;height:221px"></div>
  <p class="step-text" style="left:253px;top:22px">Holding the right hand edge<br>of the label off the surface,<br>use your squeegee and start<br>rubbing the surface using a<br>centre out motion toward the<br>right hand edge</p>
  <p class="step-note" style="left:18px;top:255px">Holding the right hand edge of the label off the surface,<br>this ensures that as you squeegee out, it releases any air bubbles<br>from getting trapped</p>
</section>

<section class="step" style="left:86px;top:790px;width:234px;height:323px">
  <div class="step-number" style="left:27px">09</div>
  <div class="photo dark" role="img" aria-label="Removing the centre masking tape strip from the label" style="left:16px;top:19px;width:198px;height:188px"></div>
  <p class="step-text" style="left:16px;top:221px">Remove the centre strip of<br>masking tape and repeat<br>steps 3 through 7 only this<br>time on the left hand side of<br>the ID Label.</p>
</section>

<section class="step" style="left:345px;top:790px;width:234px;height:323px">
  <div class="step-number" style="left:28px">10</div>
  <div class="photo mixed" role="img" aria-label="Peeling leftover masking tape from the label edge" style="left:16px;top:19px;width:199px;height:96px"></div>
  <div class="photo mixed" role="img" aria-label="Squeegee pressing down the outside label edge" style="left:16px;top:127px;width:199px;height:96px"></div>
  <p class="step-text" style="left:16px;top:235px">Remove all excess masking<br>tape and squeegee the<br>outside edges ensuring full<br>adhesion contact is made.</p>
</section>

<div class="brand-plate">Haulroad Markers</div>
<ul class="contact-list">
  <li>ABN: 00 000 000 000</li>
  <li>Unit 3, 14 Quarry Lane</li>
  <li class="cont">RIDGEFIELD&nbsp; QLD&nbsp; 4000</li>
  <li>PHONE: 07 3000 1234</li>
  <li>FAX: 07 3000 5678</li>
  <li>EMAIL: info@haulroad.example</li>
</ul>

<div class="site-address">www.haulroad.example</div>
</body>
</html>
```